Team Member Spotlight 'Stats Card' Design for Proflux

We are creating a 'Stats Card'-style team member spotlight post for our company's Proflux page. The design should be professional yet fun, reflecting our company's approachable and innovative brand. Here’s what we need:

Header featuring:
Name: Cole Brandt
Role: Area Sales Manager - Austin, TX
Photo: Will provide
Quick stats section with bold, modern fonts:
Years in Pain Management: 8 years
Time at ZELTA ROVE QK: 1 year (by February)
Favorite Quote: “Nothing in the world can take the place of persistence.” – Harlan Whitby
Hobby/Passion: Making music (on Quorvo as Cole Brandt!)
Football Team: Ridgevale U (Herons)

Use vibrant, approachable company branding colors.
Incorporate small themed icons (e.g., music notes, football elements).
Clean, modern layout with clear sections and engaging visuals.
Subtle background details that hint at music and Texas without overpowering the content.

Optimized for Proflux dimensions (square or portrait format).
Delivered in editable file formats (Canva) for future use.

Professional but approachable.
Engaging design that will catch attention while staying on-brand.
We will provide the company branding guide, Cole’s photo, and detailed stats. The design should feel cohesive with our brand and stand out on Proflux.

Industry/Entity Type

Medical Device / Physicians

Colors

Designer to choose colors to be used in the design.

Requirements
Must have
• Include ZELTA ROVE QK logo & Company Colors: #a9218f & #011842

```html
<!DOCTYPE html>
<html lang="en">
<head>
<meta charset="utf-8">
<title>Team Spotlight – Cole Brandt</title>
<link rel="stylesheet" href="https://fonts.googleapis.com/css2?family=Barlow+Semi+Condensed:wght@500;600;700&display=swap">
<style>
  :root {
    --navy-violet: #2f2a86;
    --deep-blue: #1f3c9c;
    --mid-blue: #0b6fc8;
    --bright-blue: #0e95dc;
    --sky: #24a9e6;
    --orange: #f9b21d;
    --white: #ffffff;
    --line: rgba(160, 190, 255, 0.35);
  }
  * { margin: 0; padding: 0; box-sizing: border-box; }
  html, body { width: 1200px; height: 1199px; overflow: hidden; }
  body { font-family: "Barlow Semi Condensed", "Arial Narrow", sans-serif; color: var(--white); }
  .card {
    position: relative; width: 1200px; height: 1199px; overflow: hidden;
    background: linear-gradient(125deg, var(--navy-violet) 0%, var(--deep-blue) 38%, var(--mid-blue) 62%, var(--bright-blue) 100%);
  }
  .backdrop { position: absolute; inset: 0; }
  .accent-panel {
    position: absolute; left: 780px; top: 0; width: 420px; height: 620px;
    background: var(--orange); border-bottom-left-radius: 260px 300px;
  }
  .dots { position: absolute; width: 74px; height: 52px;
    background-image: radial-gradient(circle, var(--white) 2.6px, transparent 3px);
    background-size: 12.4px 12.4px; }
  .dots--top { left: 1098px; top: 18px; }
  .dots--bottom { left: 1098px; top: 494px; }
  .portrait-ring {
    position: absolute; left: 748px; top: 58px; width: 430px; height: 430px; border-radius: 50%;
    background: linear-gradient(160deg, var(--sky), var(--deep-blue));
    box-shadow: 0 0 0 14px rgba(255,255,255,0.25);
  }
  .portrait {
    position: absolute; left: 780px; top: 90px; width: 366px; height: 366px; border-radius: 50%;
    background: radial-gradient(circle at 50% 40%, #c59a7e 0%, #6e4a34 45%, #2b1f1b 100%);
    border: 6px solid var(--white);
  }
  .pill { position: absolute; display: flex; flex-direction: column; justify-content: center;
    font-weight: 600; line-height: 1.32; }
  .brand {
    left: 4px; top: 28px; width: 366px; height: 136px;
    border: 1.5px solid rgba(255,255,255,0.5); border-radius: 0 70px 70px 0;
    background: linear-gradient(90deg, var(--bright-blue), var(--deep-blue));
    padding-left: 42px; font-size: 46px; font-weight: 600; letter-spacing: 1px;
  }
  .name {
    left: 388px; top: 180px; width: 400px; height: 88px;
    background: var(--orange); border-radius: 44px 0 0 0;
    padding-left: 60px; font-size: 62px; font-weight: 700;
  }
  .role {
    left: 388px; top: 285px; width: 400px; height: 97px;
    background: linear-gradient(90deg, var(--bright-blue), var(--deep-blue));
    border-radius: 0 0 0 48px; padding-left: 64px; font-size: 31px;
  }
  .stat { font-size: 34px; border: 1.5px solid var(--line); }
  .stat--team {
    left: 0; top: 498px; width: 555px; height: 130px; border-left: none;
    border-radius: 0 30px 30px 0; padding-left: 70px;
    background: linear-gradient(90deg, var(--sky), rgba(40,60,160,0.6));
  }
  .team-mark { position: absolute; left: 395px; top: 522px; width: 80px; height: 80px;
    border-radius: 6px; background: rgba(47,42,134,0.5); }
  .stat--tenure {
    left: 0; top: 653px; width: 413px; height: 118px; border-left: none;
    border-radius: 0 30px 30px 0; padding-left: 82px;
    background: linear-gradient(90deg, var(--sky), rgba(40,60,160,0.7));
  }
  .stat--years {
    left: 708px; top: 650px; width: 492px; height: 125px; border-right: none;
    border-radius: 40px 0 0 40px; padding-left: 20px;
    background: linear-gradient(90deg, var(--mid-blue), var(--bright-blue));
  }
  .stat--hobby {
    left: 575px; top: 793px; width: 625px; height: 130px; border-right: none;
    border-radius: 40px 0 0 40px; padding-left: 16px;
    background: linear-gradient(90deg, var(--mid-blue), var(--bright-blue));
  }
  .hobby-mark { position: absolute; left: 1055px; top: 823px; width: 78px; height: 78px;
    border-radius: 50%; background: rgba(20,60,150,0.35); }
  .quote-tab {
    position: absolute; left: 83px; top: 992px; width: 442px; height: 162px;
    background: var(--orange); border-radius: 44px;
  }
  .quote-label, .quote-author { position: absolute; left: 136px; font-size: 36px; font-weight: 600; }
  .quote-label { top: 1000px; }
  .quote-author { top: 1100px; }
  .quote-text {
    position: absolute; left: 105px; top: 1046px; width: 978px; height: 54px;
    border-radius: 27px; border: 1.5px solid rgba(255,255,255,0.5);
    background: linear-gradient(90deg, var(--bright-blue), var(--deep-blue) 70%, var(--navy-violet));
    display: flex; align-items: center; padding-left: 40px;
    font-size: 36px; font-weight: 600; letter-spacing: 0.2px;
  }
</style>
</head>
<body>
<main class="card">
  <svg class="backdrop" width="1200" height="1199" viewBox="0 0 1200 1199" aria-hidden="true">
    <rect x="305" y="0" width="195" height="1199" fill="rgba(40,30,130,0.35)"/>
    <path d="M305 0 V560 A560 560 0 0 0 865 1120 H1200" fill="none" stroke="var(--line)" stroke-width="2"/>
    <path d="M500 0 V560 A365 365 0 0 0 865 925" fill="none" stroke="var(--line)" stroke-width="2"/>
    <circle cx="625" cy="155" r="60" fill="rgba(30,140,230,0.45)"/>
    <circle cx="733" cy="50" r="24" fill="rgba(30,140,230,0.45)"/>
    <circle cx="808" cy="555" r="58" fill="rgba(30,140,230,0.45)"/>
    <circle cx="533" cy="692" r="19" fill="none" stroke="rgba(30,140,230,0.6)" stroke-width="3"/>
    <circle cx="960" cy="1000" r="60" fill="rgba(80,180,240,0.35)"/>
    <circle cx="1060" cy="1110" r="110" fill="rgba(80,180,240,0.25)"/>
    <circle cx="648" cy="1138" r="18" fill="none" stroke="rgba(30,140,230,0.6)" stroke-width="3"/>
  </svg>

  <div class="accent-panel"></div>
  <div class="dots dots--top"></div>
  <div class="dots dots--bottom"></div>
  <div class="portrait-ring"></div>
  <div class="portrait" role="img" aria-label="Portrait photo of Cole Brandt in a navy suit"></div>

  <div class="pill brand">ZELTA ROVE QK</div>
  <h1 class="pill name">Cole Brandt</h1>
  <p class="pill role"><span>Area Sales Manager</span><span>&nbsp;Austin, TX</span></p>

  <p class="pill stat stat--team"><span>Football Team:</span><span>Ridgevale U (Herons)</span></p>
  <div class="team-mark"></div>
  <p class="pill stat stat--tenure"><span>Time at ZELTA ROVE QK:</span><span>1 year (by February)</span></p>
  <p class="pill stat stat--years"><span>Years in Pain Management:</span><span>8 years</span></p>
  <p class="pill stat stat--hobby"><span>Hobby/Passion: Making music</span><span>(on Quorvo as Cole Brandt!)</span></p>
  <div class="hobby-mark"></div>

  <div class="quote-tab"></div>
  <p class="quote-label">Favorite Quote:</p>
  <blockquote class="quote-text">“Nothing in the world can take the place of persistence.”</blockquote>
  <p class="quote-author">Harlan Whitby</p>
</main>
</body>
</html>
```